Web Site Design and Business Card design for Recruiting Company

There are three major tasks in this project:
1) I need to re-design my newly created website www.talvoro.net using the same logo but creating a totally different recruiting template that will apply better for a recruitment site. I want to use the elements of the Talvoro Network logo (which is the road junction) and red, black and gray colors throughout the website. I need someone to both design and launch the site...
2) I would also like to design a double sided business card using the same logo/colors and elements as described above
3) I would also like to have a small thumbnail logo created. As our large logo cannot be previewed easily on the Pelmwork or on Google Chrome tab images

The design should be contemporary, minimalist and slick

```html
<!DOCTYPE html>
<html lang="en">
<head>
<meta charset="utf-8">
<title>Talvoro Network – Get the Career You Deserve</title>
<link href="https://fonts.googleapis.com/css2?family=Poppins:ital,wght@0,400;0,500;0,600;0,700;1,400&family=Roboto:wght@500;700;900&display=swap" rel="stylesheet">
<style>
:root{
  --red:#e3141b;
  --red-dark:#c40f15;
  --ink:#1b1b1b;
  --text:#333;
  --muted:#6b6b6b;
  --soft:#eef0f8;
  --dark:#1a1a1a;
  --footer:#1d1d1f;
  --white:#fff;
  --line:#e2e2e2;
}
*{box-sizing:border-box;margin:0;padding:0}
html,body{width:1200px;height:3593px;overflow:hidden}
body{font-family:'Poppins',sans-serif;color:var(--text);background:var(--white);position:relative}
.container{width:976px;margin:0 auto;position:relative}
h2.section-title{font-family:'Roboto',sans-serif;font-weight:700;font-size:36px;color:var(--ink);text-align:center;letter-spacing:.3px}
h2.section-title span{color:var(--red)}
.btn{display:inline-flex;align-items:center;gap:8px;background:var(--red);color:var(--white);font-weight:600;font-size:15px;border-radius:22px;padding:0 18px;height:40px;text-transform:uppercase}
.btn svg{width:14px;height:14px}

/* header */
.site-header{height:115px;border-bottom:1px solid var(--line);position:relative}
.brand{position:absolute;left:112px;top:22px;display:flex;align-items:center;gap:10px;font-weight:600;font-size:22px;color:var(--ink)}
.brand .mark{width:16px;height:16px;background:var(--red)}
.call{position:absolute;right:112px;top:12px;display:flex;align-items:center;gap:12px}
.call .icon{width:44px;height:44px;border-radius:50%;background:var(--red);display:flex;align-items:center;justify-content:center}
.call small{display:block;font-size:13px;color:var(--muted)}
.call strong{font-size:20px;color:var(--ink);font-weight:700}
.main-nav{position:absolute;right:112px;top:78px;display:flex;align-items:center;gap:34px;font-size:15px;font-weight:500;color:var(--ink)}
.main-nav .active{color:var(--red);border-bottom:2px solid var(--red);padding-bottom:4px}
.main-nav .sign-in{background:var(--red);color:var(--white);font-weight:700;border-radius:16px;padding:5px 12px;font-size:14px}

/* hero */
.hero{height:544px;position:relative;background:linear-gradient(120deg,#5b6670 0%,#3b4248 40%,#2d2f33 70%,#4e4a46 100%);overflow:hidden}
.hero .title{position:absolute;top:146px;width:100%;text-align:center;font-family:'Roboto',sans-serif;font-weight:700;font-size:52px;color:var(--white)}
.hero .lead{position:absolute;top:188px;width:100%;text-align:center;font-size:18px;font-weight:500;color:var(--white);line-height:28px;margin-top:30px}
.search-bar{position:absolute;left:155px;top:276px;width:890px;height:60px;background:rgba(255,255,255,.25);display:flex;align-items:center;gap:14px;padding:0 8px}
.field{background:var(--white);height:42px;flex:0 0 225px;display:flex;align-items:center;gap:14px;padding:0 16px;font-size:14px;color:#555}
.field .caret{margin-left:auto;border:5px solid transparent;border-top-color:#333;margin-top:5px}
.search-bar .btn{height:42px;font-size:14px;border-radius:22px}

/* welcome */
.welcome{height:386px;text-align:center;padding-top:83px}
.welcome .eyebrow{color:var(--red);font-size:18px;font-weight:500}
.welcome h1{font-family:'Roboto',sans-serif;font-weight:700;font-size:32px;color:var(--ink);margin-top:2px}
.welcome p{width:830px;margin:16px auto 0;font-size:15px;line-height:25px;color:var(--muted)}
.welcome .btn{margin-top:28px}

/* categories */
.categories{height:501px;background:var(--soft);padding-top:60px}
.categories .intro{width:700px;margin:14px auto 0;text-align:center;font-size:15px;line-height:25px;color:var(--muted)}
.cat-grid{display:flex;gap:18px;margin-top:36px}
.cat-card{flex:0 0 314px;height:242px;background:var(--white);box-shadow:0 2px 8px rgba(0,0,0,.1);padding:14px 36px}
.cat-card svg.ico{width:62px;height:62px}
.cat-card h3{font-size:17px;font-weight:500;color:var(--ink);margin-top:8px}
.cat-card ul{list-style:none;margin-top:10px}
.cat-card li{font-size:13.5px;color:var(--muted);line-height:25px;display:flex;align-items:center;gap:8px}
.cat-card li::before{content:"";width:12px;height:12px;border-radius:50%;background:var(--red);flex:none}
.cat-card .more{margin-top:12px;font-weight:700;font-size:15px;color:var(--ink)}

/* how it works */
.how{height:438px;padding-top:76px}
.steps{display:flex;margin-top:26px}
.step{flex:1;text-align:center}
.step .ring{width:98px;height:98px;border-radius:50%;border:2px dashed var(--red);margin:0 auto;position:relative;display:flex;align-items:center;justify-content:center}
.step .ring svg{width:46px;height:46px}
.step .num{position:absolute;right:4px;bottom:-6px;width:24px;height:24px;border-radius:50%;background:var(--red);color:var(--white);font-size:13px;font-weight:700;display:flex;align-items:center;justify-content:center}
.step h4{font-size:15.5px;font-weight:600;color:var(--ink);margin-top:20px}
.step p{font-size:13.5px;color:var(--muted);line-height:22px;margin-top:10px}

/* recent jobs */
.recent{height:496px;background:var(--dark);position:relative}
.recent h2{position:absolute;left:112px;top:40px;font-family:'Roboto',sans-serif;font-weight:700;font-size:36px;color:var(--white)}
.recent h2 span{color:var(--red)}
.job-card{position:absolute;left:112px;width:576px;height:132px;border:2px solid var(--red);display:flex;align-items:center;padding:0 22px}
.job-card .logo-dot{width:72px;height:72px;border-radius:50%;flex:none}
.job-card .info{margin-left:24px;color:var(--white)}
.job-card h5{font-size:19px;font-weight:500}
.job-card .co{font-size:13px;margin-top:4px}
.job-card .meta{font-size:14px;margin-top:8px;display:flex;gap:20px}
.job-card .tags{margin-left:auto;display:flex;flex-direction:column;gap:14px}
.tag{width:92px;height:28px;border-radius:14px;font-size:12px;font-weight:700;display:flex;align-items:center;justify-content:center}
.tag.full{background:var(--red);color:var(--white)}
.tag.apply{background:var(--white);color:var(--red)}
.pager{display:flex;gap:10px}
.pager span{width:24px;height:24px;border-radius:50%;background:var(--white);display:flex;align-items:center;justify-content:center}
.spotlight{position:absolute;left:777px;top:49px;width:310px;height:379px;background:var(--white)}
.spotlight .bar{height:46px;background:var(--red);color:var(--white);font-size:16px;display:flex;align-items:center;padding:0 20px}
.spotlight .bar .pager{margin-left:auto}
.spotlight .photo{margin:22px 24px 0;height:130px;background:linear-gradient(135deg,#7e96ab,#c8cfd4 55%,#6a7d8c)}
.spotlight .body{padding:14px 24px 0}
.spotlight h5{font-size:17px;font-weight:500;color:var(--ink)}
.spotlight p{font-size:13.5px;color:var(--muted);margin-top:6px}
.spotlight .btn{height:36px;font-size:14px;margin-top:12px}

/* success stories */
.success{height:553px;position:relative}
.success h2{padding-top:76px}
.story-card{position:absolute;left:130px;top:154px;width:870px;height:312px;background:var(--white);box-shadow:0 2px 10px rgba(0,0,0,.15)}
.story-card .who{position:absolute;left:34px;top:40px;display:flex;align-items:center;gap:28px;font-size:16px;font-weight:500;color:var(--ink)}
.story-card .role{background:var(--red);color:var(--white);font-size:12px;font-weight:700;border-radius:12px;padding:3px 12px}
.story-card .quote{position:absolute;left:6px;top:88px;font-family:'Roboto',sans-serif;font-size:96px;font-weight:900;color:#777;line-height:1}
.story-card blockquote{position:absolute;left:85px;top:88px;width:460px;font-style:italic;font-size:14.5px;line-height:24px;color:#555}
.story-card hr{position:absolute;left:34px;top:180px;width:500px;border:0;border-top:1px solid var(--line)}
.avatars{position:absolute;left:34px;top:210px;display:flex;gap:16px}
.avatars span{width:67px;height:67px;border-radius:50%;background:linear-gradient(135deg,#c9b7a8,#8a7468)}
.avatars span.on{box-shadow:0 0 0 3px var(--red)}
.story-card .portrait{position:absolute;left:576px;top:23px;width:269px;height:266px;background:linear-gradient(180deg,#b7b5b0,#8c8780)}
.story-nav{position:absolute;left:1031px;top:297px;display:flex;flex-direction:column;gap:20px}
.story-nav span{width:42px;height:42px;border-radius:50%;border:1px solid #bbb;display:flex;align-items:center;justify-content:center}

/* app band */
.app-band{height:252px;background:var(--red);text-align:center;color:var(--white);padding-top:48px}
.app-band h2{font-family:'Roboto',sans-serif;font-weight:700;font-size:29px}
.app-band p{width:640px;margin:14px auto 0;font-size:15.5px;line-height:25px}
.stores{display:flex;justify-content:center;gap:32px;margin-top:26px}
.store{width:162px;height:46px;background:var(--white);border-radius:4px;display:flex;align-items:center;justify-content:center;gap:10px;color:var(--ink);font-size:18px;font-weight:500}
.store i{width:18px;height:18px;background:var(--red);display:block}

/* footer */
.site-footer{height:308px;background:var(--footer);color:#ddd;position:relative}
.fcol{position:absolute;top:56px}
.fcol h6{font-size:16px;font-weight:600;color:var(--white);text-transform:none}
.fcol ul{list-style:none;margin-top:20px}
.fcol li{font-size:14px;line-height:29px}
.fcol p{font-size:14px;line-height:25px;margin-top:20px;width:310px}
.copy{position:absolute;left:0;right:0;bottom:0;height:62px;border-top:1px solid #333;text-align:center;font-size:14px;line-height:62px}
</style>
</head>
<body>

<header class="site-header">
  <div class="brand"><span class="mark"></span>Talvoro Network</div>
  <div class="call">
    <div class="icon"><svg width="20" height="20" viewBox="0 0 24 24" fill="#fff"><path d="M6.6 10.8a15 15 0 0 0 6.6 6.6l2.2-2.2c.3-.3.7-.4 1-.2 1.1.4 2.3.6 3.6.6.6 0 1 .4 1 1V20c0 .6-.4 1-1 1A17 17 0 0 1 3 4c0-.6.4-1 1-1h3.5c.6 0 1 .4 1 1 0 1.3.2 2.5.6 3.6.1.3 0 .7-.2 1z"/></svg></div>
    <div><small>Call Us Today</small><strong>+1-555-014-2290</strong></div>
  </div>
  <nav class="main-nav">
    <span class="active">Home</span><span>About Us</span><span>Jobs</span><span>Employers</span><span>Blog</span><span>Contact Us</span>
    <span class="sign-in">SIGN IN ➜</span>
  </nav>
</header>

<section class="hero" role="img" aria-label="Business professionals in suits overlaid with a network of career icons">
  <div class="title">GET THE CAREER YOU DESERVE</div>
  <p class="lead">At vero eos et accusamus et iusto odio dignissimos ducimus<br>qui blanditiis praesentium voluptatum deleniti atque</p>
  <div class="search-bar">
    <div class="field"><svg width="14" height="14" viewBox="0 0 24 24" fill="#555"><path d="M3 17.2V21h3.8L17.8 10 14 6.2zM20.7 7a1 1 0 0 0 0-1.4l-2.3-2.3a1 1 0 0 0-1.4 0L15.2 5 19 8.8z"/></svg>Job Title</div>
    <div class="field"><svg width="12" height="14" viewBox="0 0 24 24" fill="#555"><path d="M12 2a7 7 0 0 0-7 7c0 5 7 13 7 13s7-8 7-13a7 7 0 0 0-7-7zm0 9.5A2.5 2.5 0 1 1 12 6a2.5 2.5 0 0 1 0 5.5z"/></svg>Location<span class="caret"></span></div>
    <div class="field"><svg width="14" height="14" viewBox="0 0 24 24" fill="#555"><path d="M9 3h6v3h6v14H3V6h6zm2 0v3h2V3z"/></svg>Job Type<span class="caret"></span></div>
    <span class="btn"><svg viewBox="0 0 24 24" fill="none" stroke="#fff" stroke-width="3"><circle cx="10" cy="10" r="6"/><path d="m15 15 6 6"/></svg>Search Jobs</span>
  </div>
</section>

<section class="welcome">
  <div class="eyebrow">Welcome To</div>
  <h1>TALVORO NETWORK</h1>
  <p>Talvoro Network LLC is an Atlanta based talent advisory, recruiting and staffing firm. We help companies find skilled professionals within the shortest time frames though our unique network of business and personal connections nationwide and overseas.</p>
  <span class="btn">Find Jobs <svg viewBox="0 0 24 24" fill="#fff"><circle cx="12" cy="12" r="10"/><path d="m10 7 5 5-5 5" stroke="#e3141b" stroke-width="3" fill="none"/></svg></span>
</section>

<section class="categories">
  <h2 class="section-title">JOB <span>CATEGORIES</span></h2>
  <p class="intro">Sed ut perspiciatis unde omnis iste natus error sit voluptatem accusantium doloremque laudantium, totam rem aperiam, eaque ipsa quae ab illo inventore</p>
  <div class="container cat-grid">
    <div class="cat-card">
      <svg class="ico" viewBox="0 0 62 62" fill="none" stroke="#222" stroke-width="2"><rect x="4" y="6" width="54" height="36"/><path d="M24 42v10h14V42M18 54h26"/><rect x="12" y="14" width="14" height="18"/><rect x="34" y="14" width="14" height="18"/></svg>
      <h3>Information Technology (IT)</h3>
      <ul><li>Project Management</li><li>Web &amp; Application Development</li><li>Network Administration</li></ul>
      <div class="more">VIEW MORE ⊕</div>
    </div>
    <div class="cat-card">
      <svg class="ico" viewBox="0 0 62 62" fill="none" stroke="#222" stroke-width="2"><rect x="6" y="18" width="20" height="16"/><rect x="36" y="18" width="20" height="16"/><path d="M20 8h22l-4-4M42 12H20l4 4"/><path d="M6 58V44h50v14"/></svg>
      <h3>Telecommunications</h3>
      <ul><li>Project Management</li><li>Construction Management</li><li>Site Acquisition</li></ul>
      <div class="more">VIEW MORE ⊕</div>
    </div>
    <div class="cat-card">
      <svg class="ico" viewBox="0 0 62 62" fill="none" stroke="#222" stroke-width="2"><rect x="4" y="4" width="40" height="24"/><circle cx="24" cy="16" r="7"/><rect x="36" y="30" width="22" height="28"/><path d="M40 36h14M40 44h4M48 44h6M40 52h4M48 52h6M8 58V40M16 58V34M24 58V44"/></svg>
      <h3>Accounting &amp; Finance</h3>
      <ul><li>Financial Planning</li><li>Financial Management</li><li>Certified Public Accounting (CPA)</li></ul>
      <div class="more">VIEW MORE ⊕</div>
    </div>
  </div>
</section>

<section class="how">
  <h2 class="section-title">HOW IT <span>WORKS?</span></h2>
  <div class="container steps">
    <div class="step"><div class="ring"><svg viewBox="0 0 46 46" fill="none" stroke="#333" stroke-width="2"><circle cx="20" cy="14" r="8"/><path d="M6 40c0-9 6-14 14-14s10 3 12 6"/><path d="m30 38 10-10 3 3-10 10h-3z"/></svg><span class="num">1</span></div><h4>CREATE AN ACCOUNT</h4><p>Lorem ipsum dolor sit amet, consectetur adipiscing elit, sed do eiusmod tempor</p></div>
    <div class="step"><div class="ring"><svg viewBox="0 0 46 46" fill="none" stroke="#333" stroke-width="2"><rect x="10" y="4" width="26" height="38" rx="2"/><circle cx="23" cy="16" r="4"/><path d="M16 28h14M16 33h14M16 38h10"/></svg><span class="num">2</span></div><h4>COMPLETE YOUR PROFILE</h4><p>Lorem ipsum dolor sit amet, consectetur adipiscing elit, sed do eiusmod tempor</p></div>
    <div class="step"><div class="ring"><svg viewBox="0 0 46 46" fill="none" stroke="#333" stroke-width="2"><circle cx="23" cy="23" r="9"/><path d="M23 4v6M23 36v6M4 23h6M36 23h6M10 10l4 4M32 32l4 4M36 10l-4 4M10 36l4-4"/></svg><span class="num">3</span></div><h4>SEARCH YOUR JOB</h4><p>Lorem ipsum dolor sit amet, consectetur adipiscing elit, sed do eiusmod tempor</p></div>
    <div class="step"><div class="ring"><svg viewBox="0 0 46 46" fill="none" stroke="#333" stroke-width="2"><rect x="5" y="13" width="36" height="26" rx="3"/><path d="M17 13V8h12v5M5 24h36"/></svg><span class="num">4</span></div><h4>APPLY FOR JOB</h4><p>Lorem ipsum dolor sit amet, consectetur adipiscing elit, sed do eiusmod tempor</p></div>
  </div>
</section>

<section class="recent">
  <h2>RECENT <span>JOBS</span></h2>
  <div class="job-card" style="top:107px">
    <span class="logo-dot" style="background:linear-gradient(160deg,#1e86c8,#fff 50%,#1e86c8)" role="img" aria-label="Employer emblem"></span>
    <div class="info"><h5>Big Data Analytics (Ex. 1-2)</h5><div class="co">Brightline Technology Pvt. Ltd.</div><div class="meta"><span>$12K - 15k P.A.</span><span>📍 Caliphonia, PO 455001</span></div></div>
    <div class="tags"><span class="tag full">FULL TIME</span><span class="tag apply">APPLY</span></div>
  </div>
  <div class="job-card" style="top:270px">
    <span class="logo-dot" style="background:linear-gradient(180deg,#fff,#c9c2a6)" role="img" aria-label="Employer emblem"></span>
    <div class="info"><h5>Big Data Analytics (Ex. 1-2)</h5><div class="co">Brightline Technology Pvt. Ltd.</div><div class="meta"><span>$12K - 15k P.A.</span><span>📍 Caliphonia, PO 455001</span></div></div>
    <div class="tags"><span class="tag full">FULL TIME</span><span class="tag apply">APPLY</span></div>
  </div>
  <div class="pager" style="position:absolute;left:628px;top:434px"><span><svg width="10" height="10" viewBox="0 0 10 10"><path d="M7 1 3 5l4 4" stroke="#e3141b" stroke-width="2" fill="none"/></svg></span><span><svg width="10" height="10" viewBox="0 0 10 10"><path d="m3 1 4 4-4 4" stroke="#e3141b" stroke-width="2" fill="none"/></svg></span></div>
  <div class="spotlight">
    <div class="bar">Job Spotlight<div class="pager"><span><svg width="10" height="10" viewBox="0 0 10 10"><path d="M7 1 3 5l4 4" stroke="#e3141b" stroke-width="2" fill="none"/></svg></span><span><svg width="10" height="10" viewBox="0 0 10 10"><path d="m3 1 4 4-4 4" stroke="#e3141b" stroke-width="2" fill="none"/></svg></span></div></div>
    <div class="photo" role="img" aria-label="Two colleagues smiling at a computer in an office"></div>
    <div class="body"><h5>Big Data Analytics (Ex. 1-2)</h5><p>Brightline Technology Pvt. Ltd.</p><p>$12K - 15k P.A.</p><p>📍 Caliphonia, PO 455001</p><span class="btn">Add Resume</span></div>
  </div>
</section>

<section class="success">
  <h2 class="section-title">SUCCESS <span>STORIES</span></h2>
  <div class="story-card">
    <div class="who">Marcus Hale <span class="role">AUDITER</span></div>
    <div class="quote">“</div>
    <blockquote>Lorem ipsum dolor sit amet, consectetur adipiscing elit, sed do eiusmod tempor incididunt ut labore et dolore magna aliqua. Ut enim ad minim veniam, quis nostrud exercitation</blockquote>
    <hr>
    <div class="avatars" role="img" aria-label="Portraits of five placed candidates"><span></span><span class="on"></span><span></span><span></span><span></span></div>
    <div class="portrait" role="img" aria-label="Portrait of a smiling candidate with arms crossed"></div>
  </div>
  <div class="story-nav">
    <span><svg width="14" height="14" viewBox="0 0 14 14"><path d="m2 9 5-5 5 5" stroke="#333" stroke-width="2" fill="none"/></svg></span>
    <span><svg width="14" height="14" viewBox="0 0 14 14"><path d="m2 5 5 5 5-5" stroke="#333" stroke-width="2" fill="none"/></svg></span>
  </div>
</section>

<section class="app-band">
  <h2>GET TALVORO NETWORK APP FOR YOUR MOBILE</h2>
  <p>Lorem ipsum dolor sit amet, consectetur adipiscing elit, sed do eiusmod tempor incididunt ut labore et dolore magna aliqua. Ut enim ad minim veniam,</p>
  <div class="stores"><span class="store"><i></i>PlayHub</span><span class="store"><i></i>AppDock</span></div>
</section>

<footer class="site-footer">
  <div class="fcol" style="left:102px;top:60px"><h6>ABOUT OUR PRODUCT</h6><p>Lorem ipsum dolor sit amet, consectetur adipiscing elit, sed do eiusmod tempor incididunt ut labore et dolore magna aliqua. Ut enim ad minim veniam,</p></div>
  <div class="fcol" style="left:536px"><h6>MAIN MENU</h6><ul><li>Home</li><li>About Us</li><li>Jobs</li><li>Employers</li><li>Contact Us</li></ul></div>
  <div class="fcol" style="left:749px"><h6>Help</h6><ul><li>FAQ</li><li>Terms &amp; Condition</li><li>Privacy Policy</li></ul></div>
  <div class="fcol" style="left:990px"><h6>SOCIAL</h6><ul><li>Friendlane</li><li>Chirpline</li><li>Pelmwork</li><li>Snapgrid</li></ul></div>
  <div class="copy">© 2019. Talvoro Network. All rights reserved.</div>
</footer>

</body>
</html>
```